Maris Dovey Studio Business Cards

Hi - using the information and logo provided I require a two sided business card designed with the following information. The business card is a 'mini card' 3.5" x 1.25".

Front of card should be the logo attached but inverted (so the background is the peach colour and the logo white).

Back should have these details. If we can't fit the Pictogrum and Friendwall part can we just put the little logos.

Tessa Varnold

Art and Design Consultant
Dealer - Curator - Events - Styling - Creative Sourcing

P: 0438 217 604
E: tessa@marisdoveystudio.example
W: www.marisdoveystudio.example
I (pictogram image please): marisdoveystudio F (Friendwall image please): MarisDoveyAdviser

Target Market(s)

Galleries, artists, art buyers, interior design clients, event managers, creative types

Industry/Entity Type

Business

```html
<!DOCTYPE html>
<html lang="en">
<head>
<meta charset="utf-8">
<title>Maris Dovey Studio – Business Cards</title>
<link rel="stylesheet" href="https://fonts.googleapis.com/css2?family=Cormorant+Garamond:wght@500&family=Libre+Baskerville&family=Arimo&display=swap">
<style>
  :root {
    --backdrop: #9c9c9c;
    --peach: #f4baa0;
    --card-white: #ffffff;
    --ink: #5e5e62;
    --white: #ffffff;
  }
  * { margin: 0; padding: 0; box-sizing: border-box; }
  html, body {
    width: 1200px;
    height: 1098px;
    overflow: hidden;
    background: var(--backdrop);
  }
  .canvas {
    position: relative;
    width: 1200px;
    height: 1098px;
  }
  .card {
    position: absolute;
    left: 86px;
    width: 1028px;
    height: 365px;
  }
  .card--front { top: 141px; background: var(--peach); }
  .card--back { top: 600px; background: var(--card-white); }

  .front-mark {
    position: absolute;
    left: 434px;
    top: 63px;
  }
  .front-name {
    position: absolute;
    left: 0;
    right: 0;
    top: 242px;
    text-align: center;
    font-family: "Libre Baskerville", serif;
    font-size: 34px;
    letter-spacing: 7px;
    color: var(--ink);
    text-transform: uppercase;
  }

  .back-mark {
    position: absolute;
    left: 43px;
    top: 46px;
    display: flex;
    align-items: center;
    gap: 18px;
  }
  .back-mark__name {
    font-family: "Arimo", sans-serif;
    font-size: 24px;
    color: var(--peach);
  }
  .holder {
    position: absolute;
    left: 41px;
    top: 228px;
  }
  .holder__name {
    font-family: "Cormorant Garamond", serif;
    font-weight: 500;
    font-size: 54px;
    line-height: 1;
    color: var(--peach);
  }
  .holder__role {
    margin-top: 14px;
    font-family: "Arimo", sans-serif;
    font-size: 24px;
    color: var(--ink);
  }
  .contacts {
    position: absolute;
    right: 48px;
    top: 66px;
    text-align: right;
    font-family: "Arimo", sans-serif;
    font-size: 25px;
    color: var(--ink);
    line-height: 45px;
  }
  .contacts__phone { letter-spacing: 2px; }
  .socials {
    position: absolute;
    right: 48px;
    top: 242px;
    font-family: "Arimo", sans-serif;
    font-size: 25px;
    color: var(--ink);
  }
  .social {
    display: flex;
    justify-content: flex-end;
    align-items: center;
    gap: 16px;
    height: 45px;
  }
  .social__square {
    width: 29px;
    height: 29px;
    background: var(--peach);
  }
</style>
</head>
<body>
<main class="canvas">
  <section class="card card--front" aria-label="Card front">
    <svg class="front-mark" width="160" height="160" viewBox="0 0 160 160" aria-hidden="true">
      <circle cx="80" cy="80" r="78" fill="var(--white)"/>
    </svg>
    <p class="front-name">Maris Dovey Studio</p>
  </section>

  <section class="card card--back" aria-label="Card back">
    <div class="back-mark">
      <svg width="130" height="130" viewBox="0 0 130 130" aria-hidden="true">
        <circle cx="65" cy="65" r="64" fill="var(--peach)"/>
      </svg>
      <span class="back-mark__name">Maris Dovey Studio</span>
    </div>

    <div class="holder">
      <p class="holder__name">Tessa Varnold</p>
      <p class="holder__role">Art and Design Consultant</p>
    </div>

    <div class="contacts">
      <p class="contacts__phone">0438 217 604</p>
      <p>tessa@marisdoveystudio.example</p>
      <p>www.marisdoveystudio.example</p>
    </div>

    <div class="socials">
      <p class="social"><span>marisdoveystudio</span><span class="social__square" aria-hidden="true"></span></p>
      <p class="social"><span>MarisDoveyAdviser</span><span class="social__square" aria-hidden="true"></span></p>
    </div>
  </section>
</main>
</body>
</html>
```